All-Natural Head Lice Removal company

I need a business card with my pre-existing logo. We are a new company located in Portland Oregon that goes into peoples homes to help with head lice removal. My products and approach are all- natural and also will be around children.On my current logo we used Teal Bl and the color Green. I am open to new ideas just want it simple and creative

Target Market(s)

my biggest market is families of school aged children

Industry/Entity Type

Business

Contact Information for Business Card

see upload for details from previous business card

Font styles to use
Serif

Colors
33a6d7
9bcb3b
f37122

Requirements
Must have
• Basic information/ logo put into a creative format that is catching to the eye
Nice to have
• creative

```html
<!DOCTYPE html>
<html lang="en">
<head>
<meta charset="utf-8">
<title>BrightComb Business Card</title>
<link rel="stylesheet" href="https://fonts.googleapis.com/css2?family=Roboto+Slab:wght@400;700&display=swap">
<style>
  :root {
    --sky-light: #8fd3f2;
    --sky: #33a6d7;
    --sky-deep: #1a7fc4;
    --leaf: #9bcb3b;
    --ink: #2b2b2b;
    --paper: #ffffff;
    --backdrop: #ecebe8;
  }
  * { margin: 0; padding: 0; box-sizing: border-box; }
  html, body {
    width: 1200px; height: 913px; overflow: hidden;
    background: var(--backdrop);
    font-family: "Roboto Slab", Georgia, serif;
  }
  .canvas { position: relative; width: 1200px; height: 913px; }
  .card {
    position: absolute; width: 540px; height: 310px;
    border-radius: 18px; overflow: hidden;
    box-shadow: 0 10px 24px rgba(0,0,0,0.18);
  }
  .card-front { left: 70px; top: 150px; }
  .card-back { left: 590px; top: 450px;
    background: linear-gradient(160deg, var(--sky-light) 0%, var(--sky) 50%, var(--sky-deep) 100%); }
  .card-art { position: absolute; inset: 0; }
  .tagline {
    position: absolute; left: 28px; top: 26px;
    color: var(--paper); font-size: 14px; letter-spacing: 0.2px; white-space: nowrap;
  }
  .brand {
    position: absolute; display: flex; align-items: center; gap: 10px; white-space: nowrap;
  }
  .brand-dot { border-radius: 50%; background: var(--leaf); flex: none; }
  .brand-name { color: var(--ink); font-weight: 700; }
  .card-front .brand { left: 24px; top: 150px; }
  .card-front .brand-dot { width: 46px; height: 46px; }
  .card-front .brand-name { font-size: 26px; }
  .contact {
    position: absolute; right: 28px; top: 92px; text-align: right; color: var(--ink);
  }
  .contact-name { font-size: 22px; font-weight: 400; letter-spacing: 0.5px; white-space: nowrap; }
  .contact-role { color: var(--sky); font-size: 13px; letter-spacing: 1px; margin-bottom: 18px; }
  .contact-line {
    display: flex; justify-content: flex-end; align-items: center; gap: 8px;
    font-size: 14px; line-height: 22px; white-space: nowrap;
  }
  .contact-line svg { width: 13px; height: 13px; flex: none; }
  .card-back .brand { left: 50%; top: 70px; transform: translateX(-50%); }
  .card-back .brand-dot { width: 70px; height: 70px; }
  .card-back .brand-name { font-size: 42px; }
  .back-copy {
    position: absolute; left: 0; right: 0; top: 190px; text-align: center;
    color: var(--paper); font-size: 16px; line-height: 23px;
  }
</style>
</head>
<body>
<main class="canvas">
  <section class="card card-front">
    <svg class="card-art" viewBox="0 0 540 310" aria-hidden="true">
      <defs>
        <linearGradient id="frontSky" x1="0" y1="0" x2="0.4" y2="1">
          <stop offset="0" stop-color="#8fd3f2"/>
          <stop offset="0.55" stop-color="#33a6d7"/>
          <stop offset="1" stop-color="#1a7fc4"/>
        </linearGradient>
      </defs>
      <rect width="540" height="310" fill="url(#frontSky)"/>
      <path d="M400,0 C310,70 330,230 170,310 L540,310 L540,0 Z" fill="#ffffff"/>
      <path d="M400,0 C310,70 330,230 170,310" fill="none" stroke="#2b2b2b" stroke-width="12"/>
      <path d="M384,-4 C294,72 314,226 150,314" fill="none" stroke="#ffffff" stroke-width="5"/>
    </svg>
    <p class="tagline">All Natural In-Home Lice Removal Services</p>
    <div class="brand">
      <span class="brand-dot"></span>
      <span class="brand-name">BrightComb</span>
    </div>
    <div class="contact">
      <h1 class="contact-name">MARLA QUINN</h1>
      <p class="contact-role">OWNER</p>
      <p class="contact-line">1-800-555-0147
        <svg viewBox="0 0 16 16"><path d="M4 1l3 3-2 2c1 2 3 4 5 5l2-2 3 3-2 3C7 15 1 9 1 3z" fill="#33a6d7"/></svg>
      </p>
      <p class="contact-line">marla@brightcomb.com
        <svg viewBox="0 0 16 16"><rect x="1" y="3" width="14" height="10" rx="1" fill="none" stroke="#33a6d7" stroke-width="1.8"/><path d="M1 4l7 5 7-5" fill="none" stroke="#33a6d7" stroke-width="1.8"/></svg>
      </p>
      <p class="contact-line">www.brightcomb.com
        <svg viewBox="0 0 16 16"><circle cx="8" cy="8" r="6.5" fill="none" stroke="#33a6d7" stroke-width="1.6"/><path d="M1.5 8h13M8 1.5c-3 3-3 10 0 13M8 1.5c3 3 3 10 0 13" fill="none" stroke="#33a6d7" stroke-width="1.3"/></svg>
      </p>
    </div>
  </section>

  <section class="card card-back">
    <div class="brand">
      <span class="brand-dot"></span>
      <span class="brand-name">BrightComb</span>
    </div>
    <div class="back-copy">
      <p>Try BrightComb Today and Be Lice Free Tomorrow!</p>
      <p>All Natural In-Home Lice Removal Services</p>
      <p>www.brightcomb.com</p>
    </div>
  </section>
</main>
</body>
</html>
```